Professional Personal Website with Blog and four sections

I am seeking a website design for myself. I would like the site to contain a blog, related to Information Security and several sections.

I am an established Information Security Consultant (one aspect of the site).
I am an author of a children's spiritual book that is "new thought" (another aspect of the site)
I am a co-founder of a secure social platform for kids and families (www.bramlowt.com)
I may want a section on finance as well, not sure at this moment

I want this site to be a personal website, not a subscription service or professional services sales site, I want the site to look very professional, so that I can share it with all types of people without concern - business, spiritual, other.

I have provided a photo of myself for the site, smart casual on a beach. The site will be hosted on dorianhelpe.com

You can see samples of what I am referring to by searching "personal website" on images.zentrova.com

I would like the page layout, and the images chopped up as individual jpgs, including hover images for buttons. I can do the coding

I would like the following buttons
Home, About, Information Security Blog, Passion Projects, Contact

I would like the top portion of the page to say "Tobin Marsh"
I would like the subtext to say:
Executive Information Security Architect, Author, and Idea Man

I envision the following

Target Market(s)

Executive / Technical / Creative types / Spritual types

Number of Pages Required

4 page

Requirements
Must have
• Blog section
Should not have
• No Matrix themes or No Cop themes, No Fingerprints or Eyeball scans

```html
<!DOCTYPE html>
<html lang="en">
<head>
<meta charset="utf-8">
<title>Tobin Marsh</title>
<link href="https://fonts.googleapis.com/css2?family=Roboto:wght@400;500;700;900&family=Open+Sans:wght@400;600&display=swap" rel="stylesheet">
<style>
:root{
  --navy:#0d1f33;
  --navy-deep:#0a1828;
  --blue:#2f7fc3;
  --blue-dark:#1f5f99;
  --link:#2a7ab8;
  --page:#e9ebee;
  --panel:#ffffff;
  --ink:#333b44;
  --muted:#8a9199;
  --rule:#dde1e5;
  --icon:#a9b0b7;
  --footer:#16181b;
  --footer-ink:#9aa0a6;
}
*{box-sizing:border-box;margin:0;padding:0}
html,body{width:1200px;height:2272px;overflow:hidden}
body{background:var(--page);font-family:"Open Sans",Arial,sans-serif;color:var(--ink);position:relative}
.topbar{position:absolute;left:0;top:0;width:1200px;height:80px;background:var(--navy)}
.brand{position:absolute;left:100px;top:16px;font-family:"Roboto",Arial,sans-serif;font-weight:900;font-size:40px;color:#fff;letter-spacing:-0.5px}
.account{position:absolute;right:100px;top:28px;display:flex;gap:8px}
.search{width:200px;height:26px;background:#fff;border-radius:2px;position:relative}
.search svg{position:absolute;right:6px;top:6px}
.btn{height:26px;padding:0 14px;background:var(--blue);color:#fff;font:500 12px "Roboto",sans-serif;line-height:26px;border-radius:2px}
.mainnav{position:absolute;left:0;top:80px;width:1200px;height:40px;background:var(--blue)}
.mainnav ul{list-style:none;display:flex;margin-left:100px;height:40px}
.mainnav li{font:500 12px "Roboto",sans-serif;color:#fff;padding:0 20px;line-height:40px;text-transform:uppercase}
.mainnav li.active{background:var(--blue-dark)}
.hero{position:absolute;left:0;top:120px;width:1200px;height:400px;background:linear-gradient(180deg,#4f6a3a 0%,#7d9a4c 45%,#a6c25a 70%,#6f8f3a 100%)}
.features{position:absolute;left:100px;top:552px;width:1000px;display:flex;gap:24px}
.feature{width:232px}
.feature .thumb{height:128px;border:4px solid #fff}
.feature h3{margin-top:10px;font:700 14px/1.35 "Roboto",sans-serif;color:var(--link);text-transform:uppercase}
.content{position:absolute;left:100px;top:808px;width:1000px;height:1196px;background:var(--panel)}
.posts{position:absolute;left:0;top:20px;width:720px}
.post{position:relative;height:272px;border-bottom:1px solid var(--rule);margin-bottom:0}
.post .photo{position:absolute;left:0;top:10px;width:270px;height:248px}
.post .body{position:absolute;left:300px;top:16px;width:410px}
.post h2{font:700 15px/1.4 "Roboto",sans-serif;color:var(--ink)}
.post p{margin-top:10px;font-size:12px;line-height:1.7;color:var(--muted)}
.meta{margin-top:14px;display:flex;align-items:center;gap:6px}
.meta .dot{width:22px;height:22px;border-radius:50%;background:var(--icon)}
.meta time{margin-left:16px;font:500 11px "Roboto",sans-serif;color:var(--muted)}
.pager{position:absolute;left:0;top:1150px;display:flex;gap:6px}
.pager span{height:24px;min-width:24px;padding:0 8px;border:1px solid var(--rule);font:11px/22px "Roboto",sans-serif;color:var(--muted);text-align:center}
.pager span.current{background:var(--blue);color:#fff;border-color:var(--blue)}
.sidebar{position:absolute;left:740px;top:20px;width:250px}
.widget{background:#f1f3f5;padding:14px;margin-bottom:18px}
.widget h4{font:400 20px "Roboto",sans-serif;color:var(--link);margin-bottom:12px}
.about .portrait{float:left;width:70px;height:80px;background:linear-gradient(160deg,#b89a80,#6d7f94);margin:0 10px 6px 0}
.about p{font-size:11px;line-height:1.6;color:var(--muted)}
.about p:after{content:"";display:block;clear:both}
.latest li{list-style:none;display:flex;gap:10px;padding:10px 0;border-top:1px solid var(--rule)}
.latest .icon{width:40px;height:40px;flex:none;background:#d7dbe0;display:flex;align-items:center;justify-content:center}
.latest span{font-size:11px;line-height:1.5;color:var(--muted)}
.join{display:flex;align-items:center;gap:6px;margin:4px 0 22px}
.join b{font:500 14px "Roboto",sans-serif;color:var(--link);margin-right:6px}
.join i{width:22px;height:22px;background:var(--blue)}
.join i:nth-child(3){background:#55acee}
.join i:nth-child(4){background:#8a9199}
.join i:nth-child(5){background:#c7ccd1}
.newsletter{background:var(--navy);padding:16px 14px 20px}
.newsletter h4{font:400 20px "Roboto",sans-serif;color:#fff;margin-bottom:14px}
.newsletter .field{height:26px;background:#fff;margin-bottom:10px;font-size:11px;color:var(--muted);line-height:26px;padding-left:8px}
.newsletter .submit{display:inline-block;height:24px;padding:0 14px;background:#c9ced4;font:500 11px/24px "Roboto",sans-serif;color:var(--ink)}
.footer{position:absolute;left:0;top:2040px;width:1200px;height:232px;background:var(--footer)}
.cols{position:absolute;left:100px;top:24px;width:1000px;display:flex}
.col{width:250px}
.col h5{font:700 12px "Roboto",sans-serif;color:#fff;text-transform:uppercase;margin-bottom:10px}
.col .lists{display:flex;gap:30px}
.col ul{list-style:none}
.col li{font-size:11px;line-height:20px;color:var(--footer-ink)}
.col li:before{content:"› ";color:var(--blue)}
.bottom{position:absolute;left:100px;top:176px;width:1000px;height:30px;display:flex;align-items:center;justify-content:space-between;border-top:1px solid #2a2d31;padding-top:12px}
.bottom small{font-size:11px;color:var(--footer-ink)}
.social{display:flex;gap:8px}
.social i{width:22px;height:22px;border-radius:50%;background:#3b6fb6}
.social i:nth-child(2){background:#3aa7e0}
.social i:nth-child(3){background:#2f7fc3}
.social i:nth-child(4){background:#e08a2a}
.social i:nth-child(5){background:#7a7f85}
</style>
</head>
<body>
<header class="topbar">
  <div class="brand">Tobin Marsh</div>
  <div class="account">
    <div class="search"><svg width="14" height="14" viewBox="0 0 14 14"><circle cx="6" cy="6" r="4" fill="none" stroke="#8a9199" stroke-width="1.6"/><line x1="9" y1="9" x2="13" y2="13" stroke="#8a9199" stroke-width="1.6"/></svg></div>
    <span class="btn">Log in</span>
    <span class="btn">Register</span>
  </div>
</header>
<nav class="mainnav">
  <ul>
    <li class="active">Home</li><li>Who we are</li><li>What we do</li><li>What's new</li><li>Blog</li><li>Contact us</li>
  </ul>
</nav>
<div class="hero" role="img" aria-label="Children playing together on a sunny lawn"></div>

<section class="features">
  <div class="feature"><div class="thumb" role="img" aria-label="Computer screens in a security workspace" style="background:linear-gradient(135deg,#1d2a38,#3d5a78)"></div><h3>Established Information Security Consultant</h3></div>
  <div class="feature"><div class="thumb" role="img" aria-label="Child reading a book" style="background:linear-gradient(135deg,#d9b98c,#8f6f4f)"></div><h3>Author of a children's spiritual book that is "new thought"</h3></div>
  <div class="feature"><div class="thumb" role="img" aria-label="Family using a tablet together" style="background:linear-gradient(135deg,#a9c3d8,#5f7f9a)"></div><h3>Co-founder of a secure social platform for kids and families</h3></div>
  <div class="feature"><div class="thumb" role="img" aria-label="Coins stacked with a growing plant" style="background:linear-gradient(135deg,#5a3e22,#c79a4a)"></div><h3>Financial service</h3></div>
</section>

<main class="content">
  <div class="posts">
    <article class="post">
      <div class="photo" role="img" aria-label="Kids running across a park field" style="background:linear-gradient(180deg,#8fb6d8,#7fa84a)"></div>
      <div class="body">
        <h2>Aenean sed quam non sapien faucibus consequat vitae sit amet orci. Praesent quis risus.</h2>
        <p>Curabitur vel tortor sed nisl dictum tempus. Nulla facilisi morbi lacinia purus vitae mauris luctus porta. Donec ut arcu nec lectus varius aliquet eget quis felis. Integer at magna eget ligula vehicula rutrum.</p>
        <div class="meta"><i class="dot"></i><i class="dot"></i><i class="dot"></i><i class="dot"></i><i class="dot"></i><time>OCT 30, 2013</time></div>
      </div>
    </article>
    <article class="post">
      <div class="photo" role="img" aria-label="Modern school building under a blue sky" style="background:linear-gradient(180deg,#cfe0ee,#9fb3c4)"></div>
      <div class="body">
        <h2>Aenean sed quam non sapien faucibus consequat vitae sit amet orci. Praesent quis risus.</h2>
        <p>Vivamus porta nibh at erat blandit, sed volutpat ante cursus. Etiam sed lorem sit amet odio gravida finibus. Mauris non justo in velit tincidunt commodo. Sed egestas massa quis metus pretium aliquet.</p>
        <div class="meta"><i class="dot"></i><i class="dot"></i><i class="dot"></i><i class="dot"></i><i class="dot"></i><time>OCT 27, 2013</time></div>
      </div>
    </article>
    <article class="post">
      <div class="photo" role="img" aria-label="Group of smiling children lying on grass" style="background:linear-gradient(180deg,#c9a27a,#6f9a3f)"></div>
      <div class="body">
        <h2>Aenean sed quam non sapien faucibus consequat vitae sit amet orci. Praesent quis risus.</h2>
        <p>Phasellus id sem vitae nunc congue fermentum. Proin at nulla ac ipsum aliquet dapibus in non elit. Quisque tempor tortor vel quam faucibus, a laoreet justo porta. Nam eget risus sed diam.</p>
        <div class="meta"><i class="dot"></i><i class="dot"></i><i class="dot"></i><i class="dot"></i><i class="dot"></i><time>OCT 21, 2013</time></div>
      </div>
    </article>
    <article class="post">
      <div class="photo" role="img" aria-label="Boys playing football in a park" style="background:linear-gradient(180deg,#b7c9a8,#5c8a36)"></div>
      <div class="body">
        <h2>Aenean sed quam non sapien faucibus consequat vitae sit amet orci. Praesent quis risus.</h2>
        <p>Sed faucibus turpis in eros mattis, et fringilla odio tristique. Fusce vel nisi a magna pretium cursus at sit amet leo. Ut finibus libero id elit eleifend, nec posuere lacus blandit. Cras vitae.</p>
        <div class="meta"><i class="dot"></i><i class="dot"></i><i class="dot"></i><i class="dot"></i><i class="dot"></i><time>OCT 17, 2013</time></div>
      </div>
    </article>
  </div>

  <div class="pager"><span>« Prev</span><span class="current">1</span><span>2</span><span>3</span><span>4</span><span>Next »</span></div>

  <aside class="sidebar">
    <section class="widget about">
      <h4>About Me</h4>
      <div class="portrait" role="img" aria-label="Portrait of Tobin Marsh on a beach"></div>
      <p>Security architect, author and idea man. I write about protecting data, raising kind kids and building tools families can trust online every day.</p>
    </section>
    <section class="widget latest">
      <h4>Latest Articles</h4>
      <ul>
        <li><div class="icon"><svg width="16" height="16"><rect x="2" y="2" width="12" height="12" fill="none" stroke="#a9b0b7" stroke-width="1.5"/></svg></div><span>Simple steps to lock down your home network tonight</span></li>
        <li><div class="icon"><svg width="16" height="16"><rect x="2" y="2" width="12" height="12" fill="none" stroke="#a9b0b7" stroke-width="1.5"/></svg></div><span>Why passwords alone will not keep families safe</span></li>
        <li><div class="icon"><svg width="16" height="16"><rect x="2" y="2" width="12" height="12" fill="none" stroke="#a9b0b7" stroke-width="1.5"/></svg></div><span>Teaching children gratitude through daily stories</span></li>
        <li><div class="icon"><svg width="16" height="16"><rect x="2" y="2" width="12" height="12" fill="none" stroke="#a9b0b7" stroke-width="1.5"/></svg></div><span>Planning ahead: smart money habits for young parents</span></li>
      </ul>
    </section>
    <div class="join"><b>Join us on</b><i></i><i></i><i></i><i></i></div>
    <section class="newsletter">
      <h4>Newsletter Signup</h4>
      <div class="field">Name</div>
      <div class="field">Email</div>
      <span class="submit">Submit</span>
    </section>
  </aside>
</main>

<footer class="footer">
  <div class="cols">
    <div class="col"><h5>Quick links</h5><ul><li>Who we are</li><li>What we do</li><li>What's new</li><li>Blog</li><li>Contact us</li></ul></div>
    <div class="col"><h5>Links</h5><div class="lists"><ul><li>Security tips</li><li>Book news</li><li>Events</li><li>Speaking</li></ul><ul><li>Press kit</li><li>Reading list</li><li>Resources</li><li>Archive</li></ul></div></div>
    <div class="col"><h5>Links</h5><div class="lists"><ul><li>Family safety</li><li>Parent guides</li><li>Tools</li><li>FAQ</li></ul><ul><li>Partners</li><li>Careers</li><li>Support</li><li>Updates</li></ul></div></div>
    <div class="col"><h5>Links</h5><div class="lists"><ul><li>Finance</li><li>Investing</li><li>Planning</li><li>Savings</li></ul><ul><li>Privacy</li><li>Terms</li><li>Sitemap</li><li>Feedback</li></ul></div></div>
  </div>
  <div class="bottom">
    <small>Copyright © 2013 Tobin Marsh. All rights reserved.</small>
    <div class="social"><i></i><i></i><i></i><i></i><i></i></div>
  </div>
</footer>
</body>
</html>
```